Need Business Card for our Real Estate Business with Sales Executive's Picture

PANTONE 484 C ( RED)

PANTONE 2766 C ( BLUE

Industry/Entity Type

Real Estate

Contact Information for Business Card

Name, Mobile, email, & picture of Person
Agency Phone, address, Web address

Requirements
Must have
• Our Logo Colours, Agent Picture,

```html
<!DOCTYPE html>
<html lang="en">
<head>
<meta charset="utf-8">
<title>Mesa Real Estate – Business Card</title>
<link rel="stylesheet" href="https://fonts.googleapis.com/css2?family=Cinzel:wght@400;600&family=Crimson+Text:wght@400;600&display=swap">
<style>
  :root {
    --navy: #16255f;
    --navy-deep: #0d1846;
    --red: #9b1328;
    --white: #ffffff;
    --paper: #f7f7f5;
    --stage: #e6e4df;
  }
  * { box-sizing: border-box; margin: 0; padding: 0; }
  html, body { width: 1200px; height: 780px; overflow: hidden; }
  body {
    background: var(--stage);
    display: flex;
    align-items: center;
    justify-content: center;
    gap: 50px;
    font-family: "Crimson Text", Georgia, serif;
  }
  .card {
    position: relative;
    width: 540px;
    height: 310px;
    overflow: hidden;
    box-shadow: 0 6px 18px rgba(0,0,0,0.18);
  }

  /* Front */
  .card-front { background: var(--navy); }
  .card-front .backdrop { position: absolute; inset: 0; width: 100%; height: 100%; }
  .front-brand {
    position: absolute;
    left: 30px;
    top: 34px;
    width: 240px;
    font-family: "Cinzel", serif;
    font-weight: 400;
    font-size: 27px;
    letter-spacing: 3px;
    line-height: 1.25;
    color: var(--navy);
  }
  .agent-photo {
    position: absolute;
    left: 338px;
    top: 16px;
    width: 190px;
    height: 236px;
    background: linear-gradient(160deg, #d8d4cf 0%, #3a55a8 40%, #1b2f78 100%);
  }
  .agent-name {
    position: absolute;
    left: 30px;
    top: 138px;
    font-family: "Cinzel", serif;
    font-size: 15px;
    letter-spacing: 1px;
    color: var(--white);
    white-space: nowrap;
  }
  .agent-name .role { font-family: "Crimson Text", serif; font-size: 15px; letter-spacing: 0; }
  .agent-name .divider { margin: 0 8px; }
  .contact {
    position: absolute;
    left: 40px;
    top: 184px;
    color: var(--white);
    font-size: 14.5px;
    line-height: 1.3;
    list-style: none;
  }
  .contact li { display: flex; align-items: center; gap: 6px; }
  .contact .address { display: block; }
  .contact svg { width: 14px; height: 14px; flex: none; }

  /* Back */
  .card-back {
    background: radial-gradient(circle at 55% 40%, #1d2f72 0%, var(--navy) 50%, var(--navy-deep) 100%);
  }
  .back-brand {
    position: absolute;
    left: 0;
    right: 0;
    top: 96px;
    display: flex;
    align-items: center;
    justify-content: center;
    gap: 12px;
  }
  .back-brand .name {
    font-family: "Cinzel", serif;
    font-weight: 400;
    font-size: 40px;
    letter-spacing: 6px;
    color: var(--white);
    line-height: 1;
  }
  .back-brand .mark { width: 10px; height: 10px; background: var(--red); }
  .web-band {
    position: absolute;
    left: 0;
    right: 0;
    top: 234px;
    height: 34px;
    background: var(--red);
    border-top: 2px solid var(--white);
    border-bottom: 2px solid var(--white);
    box-shadow: 0 -5px 0 var(--navy-deep), 0 5px 0 var(--navy-deep);
    display: flex;
    align-items: center;
    padding-left: 52px;
    color: var(--white);
    font-family: "Cinzel", serif;
    font-size: 13px;
    letter-spacing: 3px;
  }
</style>
</head>
<body>

  <section class="card card-front" aria-label="Business card front">
    <svg class="backdrop" viewBox="0 0 540 310" preserveAspectRatio="none" aria-hidden="true">
      <polygon points="0,0 330,0 282,130 0,130" fill="#f7f7f5"/>
      <polygon points="0,130 282,130 330,0 358,0 298,166 0,166" fill="#9b1328"/>
      <line x1="298" y1="167" x2="360" y2="0" stroke="#ffffff" stroke-width="2"/>
      <line x1="0" y1="167" x2="298" y2="167" stroke="#ffffff" stroke-width="1"/>
    </svg>
    <div class="front-brand">MESA<br>REAL ESTATE</div>
    <div class="agent-photo" role="img" aria-label="Portrait photo of the sales executive in a blue suit"></div>
    <p class="agent-name">DANIEL REEVE<span class="divider">|</span><span class="role">Owner</span></p>
    <ul class="contact">
      <li class="address">PO BOX 456 Harbour Lane<br>3rd street Geelong</li>
      <li>
        <svg viewBox="0 0 16 16" aria-hidden="true"><circle cx="8" cy="8" r="7" fill="none" stroke="#fff"/><path d="M5.5 4.5l1.5 1.5-1 1a5 5 0 0 0 3 3l1-1 1.5 1.5-1 1C7.5 11.5 4.5 8.5 4.5 5.5z" fill="#fff"/></svg>
        (555) 018-2247
      </li>
      <li>
        <svg viewBox="0 0 16 16" aria-hidden="true"><circle cx="8" cy="8" r="7" fill="none" stroke="#fff"/><rect x="4" y="5.5" width="8" height="5.5" fill="none" stroke="#fff"/><path d="M4 5.5l4 3 4-3" fill="none" stroke="#fff"/></svg>
        hello@mesarealty.com
      </li>
      <li>
        <svg viewBox="0 0 16 16" aria-hidden="true"><circle cx="8" cy="8" r="7" fill="none" stroke="#fff"/><circle cx="8" cy="8" r="4" fill="none" stroke="#fff"/><path d="M4 8h8M8 4v8" stroke="#fff"/></svg>
        www.mesarealty.com
      </li>
    </ul>
  </section>

  <section class="card card-back" aria-label="Business card back">
    <div class="back-brand">
      <span class="mark"></span>
      <span class="name">MESA REAL ESTATE</span>
    </div>
    <div class="web-band">www.MESAREALTY.com</div>
  </section>

</body>
</html>
```